Structural Engineering Business Card

Brookvane Drafting does residential house plans for clients in Central Florida. Would like simple but elegant business card that is appropriate for a house plan engineering company. Prefer black business card with black/white them but open to other shades of blue. I uploaded a sample card that I came across that looked good but please come up with your own creative designs.

Contact Information for Business Card

Name, Title, Phone, Email, Address, website

```html
<!DOCTYPE html>
<html lang="en">
<head>
<meta charset="utf-8">
<title>Brookvane Drafting – Business Card</title>
<link rel="stylesheet" href="https://fonts.googleapis.com/css2?family=Inter:wght@300;400;700;800&display=swap">
<style>
  :root {
    --page-bg: #2b2b2d;
    --card-bg: #1f1f20;
    --ink: #ffffff;
    --ink-soft: #e6e6e6;
    --rule: #cfcfcf;
  }
  html, body {
    margin: 0;
    width: 1200px;
    height: 900px;
    overflow: hidden;
    background: var(--page-bg);
    font-family: "Inter", Arial, sans-serif;
  }
  .canvas {
    position: relative;
    width: 1200px;
    height: 900px;
  }
  .card {
    position: absolute;
    left: 100px;
    top: 165px;
    width: 1000px;
    height: 571px;
    background: var(--card-bg);
    color: var(--ink);
    box-shadow: 0 12px 40px rgba(0,0,0,0.45);
  }
  .holder {
    position: absolute;
    left: 64px;
    top: 62px;
  }
  .holder-name {
    margin: 0;
    font-weight: 800;
    font-size: 34px;
    letter-spacing: 0.5px;
    text-transform: uppercase;
    line-height: 1.1;
  }
  .holder-title {
    margin: 4px 0 0;
    font-weight: 300;
    font-size: 25px;
    color: var(--ink-soft);
  }
  .divider {
    position: absolute;
    left: 64px;
    right: 70px;
    top: 232px;
    height: 1.5px;
    background: var(--rule);
  }
  .contact-list {
    position: absolute;
    left: 64px;
    top: 258px;
    margin: 0;
    padding: 0;
    list-style: none;
  }
  .contact-item {
    display: flex;
    align-items: center;
    gap: 12px;
    font-size: 24px;
    font-weight: 400;
    line-height: 1.45;
  }
  .contact-icon {
    width: 18px;
    height: 18px;
    fill: var(--ink);
    flex: none;
  }
  .brand {
    position: absolute;
    right: 80px;
    top: 120px;
    display: flex;
    align-items: center;
    gap: 16px;
  }
  .brand-mark {
    width: 26px;
    height: 26px;
    background: var(--ink);
  }
  .brand-name {
    font-weight: 800;
    font-size: 44px;
    letter-spacing: 0.5px;
    color: var(--ink);
  }
  .address {
    position: absolute;
    right: 80px;
    bottom: 62px;
    margin: 0;
    font-style: normal;
    text-align: right;
    font-size: 24px;
    line-height: 1.35;
  }
</style>
</head>
<body>
<div class="canvas">
  <section class="card">
    <div class="holder">
      <h1 class="holder-name">Daniel Whitcombe</h1>
      <p class="holder-title">Founder/CEO</p>
    </div>

    <div class="brand">
      <span class="brand-mark"></span>
      <span class="brand-name">Brookvane Drafting</span>
    </div>

    <div class="divider"></div>

    <ul class="contact-list">
      <li class="contact-item">
        <svg class="contact-icon" viewBox="0 0 24 24" aria-hidden="true"><path d="M6.6 10.8a15.1 15.1 0 0 0 6.6 6.6l2.2-2.2a1 1 0 0 1 1-.25 11.4 11.4 0 0 0 3.6.57 1 1 0 0 1 1 1V20a1 1 0 0 1-1 1A17 17 0 0 1 3 4a1 1 0 0 1 1-1h3.5a1 1 0 0 1 1 1c0 1.25.2 2.45.57 3.57a1 1 0 0 1-.25 1z"/></svg>
        407.555.0182
      </li>
      <li class="contact-item">
        <svg class="contact-icon" viewBox="0 0 24 24" aria-hidden="true"><path d="M2 5h20v14H2z M2 5l10 8 10-8" fill="none" stroke="#fff" stroke-width="2"/></svg>
        info@brookvanedrafting.com
      </li>
      <li class="contact-item">
        <svg class="contact-icon" viewBox="0 0 24 24" aria-hidden="true"><circle cx="12" cy="12" r="9" fill="none" stroke="#fff" stroke-width="2"/><path d="M3 12h18M12 3c3 3 3 15 0 18M12 3c-3 3-3 15 0 18" fill="none" stroke="#fff" stroke-width="1.5"/></svg>
        www.brookvanedrafting.com
      </li>
    </ul>

    <address class="address">
      2710 Cedar Row Suite 140<br>
      Lakeview, FL 32801
    </address>
  </section>
</div>
</body>
</html>
```